Business Card Design needed for start up company Halvora

In need of a new business card designed for a start up company based in Sydney, Halvora is a new start up innovative Company, our mission it to make property accessible for everyday Australian and to become the leading Real Estate platform in Australia. We want it to be fresh and clean.

Industry/Entity Type

Financial

Contact Information for Business Card

Section for Name
Section for Title

HALVORA - The Strength of Pooling
Mobile:
Direct:

Font styles to use
Sans Serif

Colors
33a6d7
0692cd
0255a3
ffffff

Requirements
Must have
• Logo, all business card details

```html
<!DOCTYPE html>
<html lang="en">
<head>
<meta charset="utf-8">
<title>Halvora Business Card</title>
<link rel="stylesheet" href="https://fonts.googleapis.com/css2?family=Montserrat:wght@500;700;800&display=swap">
<style>
  :root {
    --navy: #1e3f7e;
    --sky: #33a6d7;
    --ocean: #0692cd;
    --royal: #0255a3;
    --white: #ffffff;
    --paper: #f3f3f3;
    --backdrop: #e6e8eb;
  }
  * { box-sizing: border-box; margin: 0; padding: 0; }
  html, body { width: 1200px; height: 886px; overflow: hidden; }
  body {
    background: var(--backdrop);
    font-family: "Montserrat", Arial, sans-serif;
    display: flex;
    flex-direction: column;
    align-items: center;
    justify-content: center;
    gap: 60px;
  }
  .card {
    position: relative;
    width: 600px;
    height: 343px;
    border-radius: 18px;
    overflow: hidden;
    box-shadow: 0 10px 28px rgba(0,0,0,.18);
  }
  .brand {
    display: flex;
    align-items: center;
    gap: 10px;
    font-weight: 800;
    letter-spacing: -0.5px;
  }
  .brand-dot {
    width: 46px; height: 46px;
    border-radius: 50%;
    background: var(--sky);
  }

  /* back */
  .card-back {
    background: var(--navy);
    display: flex;
    flex-direction: column;
    align-items: center;
    justify-content: center;
  }
  .card-back .brand { color: var(--white); font-size: 52px; }
  .card-back .brand-dot { width: 60px; height: 60px; }
  .tagline {
    margin-top: 34px;
    color: var(--white);
    font-size: 15px;
    font-weight: 500;
    letter-spacing: .3px;
  }

  /* front */
  .card-front { background: var(--paper); }
  .card-front .arc { position: absolute; inset: 0; }
  .card-front .brand {
    position: absolute;
    top: 62px; right: 50px;
    color: var(--navy);
    font-size: 40px;
  }
  .contact {
    position: absolute;
    left: 28px; top: 170px;
    color: var(--white);
    font-size: 12.5px;
    font-weight: 500;
    line-height: 1.45;
  }
  .contact .address { margin-bottom: 6px; }
  .contact li { list-style: none; display: flex; align-items: center; gap: 8px; }
  .contact svg { width: 12px; height: 12px; flex: none; }
  .person {
    position: absolute;
    right: 50px; bottom: 46px;
  }
  .person-name { color: var(--navy); font-size: 21px; font-weight: 700; }
  .person-title { color: var(--sky); font-size: 15px; font-weight: 700; }
</style>
</head>
<body>

  <section class="card card-back">
    <div class="brand"><span class="brand-dot"></span><span>HALVORA</span></div>
    <p class="tagline">The Strength of Pooling</p>
  </section>

  <section class="card card-front">
    <svg class="arc" viewBox="0 0 600 343" width="600" height="343" aria-hidden="true">
      <circle cx="40" cy="340" r="214" fill="none" stroke="var(--sky)" stroke-width="8"/>
      <circle cx="30" cy="340" r="206" fill="var(--navy)"/>
    </svg>

    <div class="contact">
      <p class="address">42 Wattle Grove<br>Surry Hills, NSW 2010</p>
      <ul>
        <li>
          <svg viewBox="0 0 12 12"><path d="M2.5 1 L4.5 1 L5.3 3.6 L4 4.6 Q5 7 7.4 8 L8.4 6.7 L11 7.5 L11 9.5 Q10.5 11 9 11 Q1 10 1 3 Q1 1.5 2.5 1Z" fill="var(--sky)"/></svg>
          0412 558 903
        </li>
        <li>
          <svg viewBox="0 0 12 12"><rect x="3" y="0.5" width="6" height="11" rx="1" fill="none" stroke="var(--sky)" stroke-width="1.2"/><circle cx="6" cy="9.5" r=".7" fill="var(--sky)"/></svg>
          02 9187 4460
        </li>
        <li>
          <svg viewBox="0 0 12 12"><rect x="0.5" y="2.5" width="11" height="7" fill="var(--sky)"/><path d="M0.5 2.5 L6 6.5 L11.5 2.5" fill="none" stroke="var(--navy)" stroke-width="1"/></svg>
          liam@halvora.com
        </li>
        <li>
          <svg viewBox="0 0 12 12"><circle cx="6" cy="6" r="5.5" fill="var(--sky)"/><path d="M0.5 6 H11.5 M6 0.5 Q3 6 6 11.5 M6 0.5 Q9 6 6 11.5" fill="none" stroke="var(--navy)" stroke-width=".8"/></svg>
          www.halvora.com
        </li>
      </ul>
    </div>

    <div class="brand"><span class="brand-dot"></span><span>HALVORA</span></div>

    <div class="person">
      <p class="person-name">LIAM CARTER</p>
      <p class="person-title">CEO/FOUNDER</p>
    </div>
  </section>

</body>
</html>
```